Real Estate Website

We currently have an existing site at https://keyplumtrevalder.com.au/ but require a much more professional design.

We like the style/design of the following which are competitors : https://tovimarla.com.au/
https://www.glenvaroxi.com.au/
https://lumetravosk.com.au/

```html
<!DOCTYPE html>
<html lang="en">
<head>
<meta charset="utf-8">
<title>Keyplum Trevalder – Sell or Rent Your Property Yourself</title>
<link href="https://fonts.googleapis.com/css2?family=Lato:ital,wght@0,400;0,700;0,900;1,400&display=swap" rel="stylesheet">
<style>
:root{
  --navy:#2b2159;
  --navy-deep:#231a4a;
  --red:#cf2029;
  --grey-bg:#ededed;
  --text:#333;
  --white:#fff;
}
*{box-sizing:border-box;margin:0;padding:0}
html,body{width:1200px;height:3508px;overflow:hidden}
body{font-family:'Lato',sans-serif;color:var(--text);background:var(--white);position:relative}
.abs{position:absolute}
a{color:inherit;text-decoration:none}

/* header */
.site-header{left:0;top:0;width:1200px;height:128px;background:#efefef}
.brand{left:75px;top:92px;font-size:18px;font-weight:700;color:var(--navy)}
.brand-mark{left:147px;top:22px;width:36px;height:36px;border:3px solid var(--red);border-radius:50%}
.main-nav{left:294px;top:56px;font-size:12.5px;font-weight:700;color:var(--navy);letter-spacing:.2px}
.main-nav a{position:absolute;white-space:nowrap}
.main-nav .active{border-bottom:2px solid var(--navy);padding-bottom:6px}
.btn-login{left:974px;top:45px;width:151px;height:38px;border-radius:19px;background:var(--red);color:#fff;font-size:12.5px;font-weight:700;display:flex;align-items:center;justify-content:center}

/* hero */
.hero-photo{left:0;top:128px;width:1200px;height:693px;background:linear-gradient(120deg,#8a6a4a 0%,#5e4a44 35%,#4a3c52 65%,#2f2847 100%)}
.tab{top:207px;height:53px;background:var(--red);color:#fff;font-size:19px;font-weight:700;border-radius:8px 8px 0 0;display:flex;align-items:center;justify-content:center}
.calc-card{left:75px;top:260px;width:512px;height:482px;background:#fff;border-radius:0 10px 10px 10px}
.calc-row{position:absolute;left:24px;right:24px;display:flex;justify-content:space-between;font-size:17.5px;font-weight:700;color:var(--navy-deep)}
.calc-row .val{color:var(--red)}
.slider{position:absolute;left:24px;right:24px;height:8px;border-radius:4px;background:#d6d6d6}
.slider .fill{height:100%;background:var(--navy);border-radius:4px}
.slider .knob{position:absolute;top:-9px;width:26px;height:26px;border-radius:50%;background:var(--navy)}
.pill-out{position:absolute;border:2px solid var(--navy);border-radius:26px;display:flex;align-items:center;justify-content:center}
.calc-label{position:absolute;left:24px;font-size:17.5px;font-weight:700;color:var(--navy-deep)}
.total{position:absolute;left:24px;top:400px;font-size:42px;font-weight:900;color:var(--navy)}

/* listing band */
.band{left:0;top:821px;width:1200px;height:168px;background:#ececec}
.band-dark{left:0;top:821px}
.band-text{left:75px;top:852px;color:#fff;font-size:30px;font-weight:700;line-height:38px}
.band-sub{left:75px;top:939px;color:#fff;font-size:19px;font-style:italic}
.partner{top:880px;font-size:34px;font-weight:700;color:var(--navy)}

/* about */
.section-title{color:var(--navy);font-weight:900}
.body-copy{font-size:16.5px;line-height:31.5px;color:#444}
.btn-red{height:55px;border-radius:28px;background:var(--red);color:#fff;font-size:22px;font-weight:700;display:flex;align-items:center;justify-content:center}

/* savings */
.savings-bg{left:0;top:1637px;width:1200px;height:283px;background:var(--grey-bg)}
.feature{top:1822px;width:250px;height:196px;background:#fff;border:4px solid #e4e4e4;border-radius:12px;display:flex;flex-direction:column;align-items:center;padding-top:28px}
.feature svg{width:64px;height:56px}
.feature h3{margin-top:18px;color:var(--red);font-size:24px;font-weight:700;line-height:29px;text-align:center}

/* guide */
.guide{left:0;top:2643px;width:1200px;height:525px;background:linear-gradient(180deg,#2d1f63 0%,#3a2a6e 45%,#402a5e 75%,#2a1d4d 100%)}
.field{background:#fff;border-radius:28px;font-size:15px;color:#333;padding:0 23px;display:flex;align-items:center}

/* footer */
.foot-title{font-size:23px;font-weight:700;color:var(--navy)}
.foot-text{font-size:13.5px;line-height:26px;color:#333}
.socials{left:887px;top:3400px;display:flex;gap:14px;font-size:14px;font-weight:700;color:var(--navy)}
</style>
</head>
<body>

<header class="abs site-header">
  <div class="abs brand-mark"></div>
  <div class="abs brand">Keyplum Trevalder</div>
  <nav class="abs main-nav">
    <a class="active" style="left:0">HOME</a>
    <a style="left:72px">SELL</a>
    <a style="left:132px">RENT</a>
    <a style="left:198px">ADD ON SERVICE</a>
    <a style="left:339px">USEFUL RESOURCES</a>
    <a style="left:499px">ABOUT</a>
    <a style="left:576px">CONTACT US</a>
  </nav>
  <a class="abs btn-login">MEMBER LOGIN</a>
</header>

<section>
  <div class="abs hero-photo" role="img" aria-label="Happy family with a child on the father's back in front of a brick house"></div>
  <div class="abs tab" style="left:75px;width:195px">Sell My Property</div>
  <div class="abs tab" style="left:276px;width:197px">Rent My Property</div>
  <div class="abs calc-card">
    <div class="calc-row" style="top:32px"><span>Property Value</span><span class="val">$50000</span></div>
    <div class="slider" style="top:75px"><div class="fill" style="width:42%"></div><div class="knob" style="left:calc(42% - 13px)"></div></div>
    <div class="calc-row" style="top:96px"><span>Agent Commission (%)</span><span class="val">2.5%</span></div>
    <div class="slider" style="top:139px"><div class="fill" style="width:19%"></div><div class="knob" style="left:calc(19% - 13px)"></div></div>
    <div class="calc-row" style="top:163px"><span>Marketing Fee ($)</span><span class="val">+5000</span></div>
    <div class="slider" style="top:205px"><div class="fill" style="width:42%"></div><div class="knob" style="left:calc(42% - 13px)"></div></div>
    <div class="calc-label" style="top:244px">Estimated Total Spend With Agent ($)</div>
    <div class="pill-out" style="left:349px;top:232px;width:139px;height:47px;font-size:25px;font-weight:700;color:var(--navy)">40350</div>
    <div class="calc-label" style="top:311px">Select Our Package</div>
    <div class="pill-out" style="left:200px;top:298px;width:288px;height:47px;justify-content:space-between;padding:0 18px;font-size:16.5px;color:#333">Select Package
      <svg width="10" height="14" viewBox="0 0 10 14"><path d="M5 0l4 5H1zM5 14L1 9h8z" fill="#333"/></svg></div>
    <div class="calc-label" style="top:370px;font-size:21px">Total Saving With Our Package</div>
    <div class="total">39851</div>
  </div>
</section>

<section>
  <div class="abs band"></div>
  <svg class="abs band-dark" width="500" height="168" viewBox="0 0 500 168"><polygon points="0,0 494,0 447,168 0,168" fill="#2b2159"/></svg>
  <div class="abs band-text">Keyplum Trevalder helps<br>you to list on</div>
  <div class="abs band-sub">+ more sites</div>
  <div class="abs partner" style="left:540px">Homevista</div>
  <div class="abs partner" style="left:903px">Parcelo</div>
</section>

<section>
  <svg class="abs" style="left:0;top:1072px" width="587" height="477" viewBox="0 0 587 477" role="img" aria-label="Excited couple celebrating beside a sold sign in front of their modern house"><path d="M0,30 L560,0 Q587,0 587,25 L587,450 Q587,477 560,477 L0,440 Z" fill="#a9a59c"/></svg>
  <h2 class="abs section-title" style="left:616px;top:1100px;font-size:54px;line-height:56px">About<br>Keyplum Trevalder</h2>
  <p class="abs body-copy" style="left:616px;top:1232px;width:510px">Keyplum Trevalder is an Australia real estate expert who can help you to sell, rent&nbsp; your properties yourself and&nbsp; save thousands of dollars as traditional agent himself found that the landlord always get charged too much for no matter selling, renting&nbsp; their home by the agents. But someone will ask wait can I&nbsp; sell and rent my property by myself?</p>
  <a class="abs btn-red" style="left:616px;top:1457px;width:196px">Read More</a>
</section>

<section>
  <div class="abs savings-bg"></div>
  <h2 class="abs section-title" style="left:0;width:1200px;top:1692px;text-align:center;font-size:38px;line-height:45px;font-weight:700">How much could you save by selling with<br>Keyplum Trevalder?</h2>
  <div class="abs feature" style="left:71px">
    <svg viewBox="0 0 64 56" fill="none" stroke="#2b2159" stroke-width="2"><circle cx="24" cy="26" r="10"/><circle cx="24" cy="26" r="4"/><circle cx="48" cy="12" r="6" stroke="#cf2029"/><circle cx="48" cy="40" r="6"/><path d="M24 12v-4M24 44v-4M10 26H6M42 26h-4M14 16l-3-3M37 39l-3-3M14 36l-3 3M37 13l-3 3"/></svg>
    <h3>You are in<br>Control</h3>
  </div>
  <div class="abs feature" style="left:340px">
    <svg viewBox="0 0 64 56" fill="none" stroke="#2b2159" stroke-width="2"><rect x="12" y="4" width="40" height="32" rx="2"/><rect x="16" y="8" width="32" height="24"/><path d="M4 44h56v4H4z"/><path d="M8 40h48"/></svg>
    <h3>Easy to<br>Use</h3>
  </div>
  <div class="abs feature" style="left:610px">
    <svg viewBox="0 0 64 56" fill="none" stroke="#2b2159" stroke-width="2"><rect x="4" y="14" width="56" height="28"/><circle cx="32" cy="28" r="8" stroke="#cf2029"/><path d="M4 20h6v-6M54 14v6h6M4 36h6v6M54 42v-6h6"/></svg>
    <h3>Huge<br>Savings</h3>
  </div>
  <div class="abs feature" style="left:881px">
    <svg viewBox="0 0 64 56" fill="none" stroke="#2b2159" stroke-width="2"><path d="M6 22c0-9 9-16 20-16s20 7 20 16-9 16-20 16c-3 0-5 0-8-1l-9 5 2-7C8 32 6 27 6 22z"/><path d="M48 20c6 3 10 8 10 13 0 4-2 7-4 9l2 7-8-4c-3 1-5 1-8 1-6 0-11-2-14-6" stroke="#cf2029"/></svg>
    <h3>Great<br>Support</h3>
  </div>
</section>

<section>
  <h2 class="abs section-title" style="left:75px;top:2142px;font-size:54px">Add on Services</h2>
  <p class="abs body-copy" style="left:75px;top:2220px;width:495px">Lorem ipsum dolor sit amet, consectetur adipiscing elit, sed do eiusmod tempor incididunt ut labore et dolore magna aliqua. Ut enim ad minim veniam, quis nostrud exercitation ullamco laboris nisi ut aliquip ex ea commodo consequat. Duis aute irure dolor in reprehenderit in voluptate velit esse cillum dolore eu fugiat nulla pariatur.</p>
  <a class="abs btn-red" style="left:75px;top:2438px;width:196px">Read More</a>
  <svg class="abs" style="left:616px;top:2084px" width="584" height="477" viewBox="0 0 584 477" role="img" aria-label="Agent meeting a young couple over a laptop in a bright office"><path d="M25,0 L584,12 L584,440 L25,477 Q0,477 0,452 L0,25 Q0,0 25,0 Z" fill="#b8b0a8"/></svg>
</section>

<section>
  <div class="abs guide" role="img" aria-label="City skyline lit up at night with a purple tint"></div>
  <h2 class="abs" style="left:0;width:1200px;top:2720px;text-align:center;color:#fff;font-size:38px;font-weight:700">Free E-Guide for Selling/Renting your Property</h2>
  <div class="abs field" style="left:253px;top:2804px;width:331px;height:56px">Name</div>
  <div class="abs field" style="left:616px;top:2804px;width:329px;height:56px">Email Address</div>
  <div class="abs field" style="left:253px;top:2881px;width:692px;height:125px;border-radius:12px;align-items:flex-start;padding-top:22px">Message</div>
  <a class="abs btn-red" style="left:503px;top:3024px;width:194px;height:54px">Read More</a>
</section>

<footer>
  <div class="abs brand-mark" style="left:150px;top:3255px;width:46px;height:46px"></div>
  <div class="abs" style="left:75px;top:3333px;font-size:21px;font-weight:700;color:var(--navy)">Keyplum Trevalder</div>
  <div class="abs foot-text" style="left:75px;top:3377px">Copyright@2021 Keyplum Trevalder<br>All Right Reserved<br>Terms of Use&nbsp; /&nbsp; Privacy Policy</div>

  <div class="abs foot-title" style="left:345px;top:3227px">Keyplum Trevalder</div>
  <p class="abs foot-text" style="left:345px;top:3264px;width:240px">Keyplum Trevalder can help you to sell or rent your home yourself with no agent commission. 100% transparency of the sale or rental process. You take 100% of the control to sell/rent your property. Start today and save thousands of agent commission.</p>

  <div class="abs foot-title" style="left:676px;top:3227px">Site Map</div>
  <div class="abs foot-text" style="left:676px;top:3260px;line-height:27.5px">Home<br>Sell<br>Rent<br>Add on Service<br>Useful Resources<br>About<br>Contact Us</div>

  <div class="abs foot-title" style="left:887px;top:3227px">Contact Us</div>
  <div class="abs foot-text" style="left:887px;top:3265px;font-size:14.5px;line-height:29px">1300648219<br>info@keyplumtrevalder.com.au</div>
  <div class="abs foot-title" style="left:887px;top:3361px">Follow Us</div>
  <div class="abs socials"><span>Kovo</span><span>Chirpa</span><span>Snapra</span><span>Linto</span><span>Vidmo</span></div>
</footer>

</body>
</html>
```